Ridge Lass Crew (Flyer)

I want a flyer to advertise my service.
Details below, and logo's to use are attached.

A girls only after school program, 11-14yrs, as OSHC is no longer avail, dedicated to coaching & mentoring our girls into strong, independent young women.

The Brainchild of Rebecca Folwin, Ridge Lass Crew was created to address the growing demand for after school/school holiday supervision for kids moving from primary into high school, when OSHC ceases to exist.
With over 12 years experience mentoring and coaching young women in the corporate world, Bec decided to leave her role as a Director with Tarrant Trust, and follow her passion.
Bec, along with her sister Lorraine, who has over 10 years experience in local communities as a Youth Worker, and is also a qualified Enrolled Nurse, embarked on building a program designed to keep parents happy (by knowing their girls are safe) and dedicated to coaching and mentoring our girls into strong, independent young women.
Open every afternoon and during school holidays, we look to offer;
- Daily meditation
- Healthy snacks
- Dedicated homework time
- Organised group activity, led by qualified instructors (yoga, fitness class, soccer etc)
- Regular guests speakers, addressing issues/concerns for young people today
- SOCIAL MEDIA FREE ZONE

Located 87 Pelham Pde, Baulkham Hills (across from Crestmoor Day Clinic)
Open 3-6pm Monday to Friday

Facebook page: http://fb.example/ridgelasscrew
Email: info@ridgelasscrew.example.au
Mobile: 0455817396

Target Market(s)

Parents of teenage girls, teenage girls 11-14 years

Industry/Entity Type

School

Font styles to use
Sans Serif

Colors
b768aa
e667a6

Requirements
Must have
• What progam is - see brief
• Who runs it
Should not have
• Not be too busy, not overly mature images

```html
<!DOCTYPE html>
<html lang="en">
<head>
<meta charset="utf-8">
<title>Ridge Lass Crew – After School Program Flyer</title>
<link rel="stylesheet" href="https://fonts.googleapis.com/css2?family=Cinzel:wght@400;700&family=Open+Sans:wght@400;600;700&family=Oswald:wght@300;400&family=Roboto+Condensed:wght@700&display=swap">
<style>
  :root {
    --violet: #c283dc;
    --violet-deep: #b768aa;
    --magenta: #e667a6;
    --magenta-strong: #e04bb4;
    --blush: #f8c2f2;
    --plum: #3b1740;
    --offer-red: #e2306f;
    --white: #ffffff;
    --photo-light: #f4f1f2;
    --photo-mid: #dcdadb;
    --photo-mint: #bfe3dc;
  }
  * { box-sizing: border-box; margin: 0; padding: 0; }
  html, body { width: 934px; height: 1200px; overflow: hidden; background: var(--violet); }
  .flyer {
    position: relative; width: 934px; height: 1200px; overflow: hidden;
    font-family: "Open Sans", sans-serif; color: var(--plum);
  }
  .flyer-shapes { position: absolute; inset: 0; }

  .brand-box {
    position: absolute; left: 16px; top: 28px; width: 268px; height: 364px;
    background: var(--white);
    display: flex; align-items: center; justify-content: center; text-align: center;
  }
  .brand-name {
    font-family: "Cinzel", serif; font-weight: 700; font-size: 46px; line-height: 1.15;
    color: var(--magenta-strong);
  }

  .headline-box {
    position: absolute; left: 480px; top: 164px; width: 408px; height: 224px;
    background: var(--magenta-strong); border-radius: 8px;
    text-align: center; padding-top: 14px;
  }
  .headline-box .line { font-family: "Cinzel", serif; font-weight: 700; line-height: 1.1; color: var(--plum); }
  .headline-box .l1 { font-size: 38px; letter-spacing: 1px; }
  .headline-box .l2 { font-size: 27px; margin-top: 8px; }
  .headline-box .l3 { font-size: 37px; margin-top: 8px; letter-spacing: 1px; }
  .headline-box .note { font-family: "Open Sans", sans-serif; font-weight: 700; font-size: 19px; margin-top: 6px; color: var(--plum); }

  .section-title {
    position: absolute; left: 66px; font-family: "Open Sans", sans-serif; font-weight: 700;
    font-size: 29px; color: var(--offer-red); letter-spacing: 0.5px;
  }
  .offer-title { top: 470px; }
  .about-title { top: 798px; }

  .offer-list { position: absolute; left: 64px; top: 522px; list-style: none; width: 380px; }
  .offer-list li {
    position: relative; padding-left: 22px; font-size: 19px; font-weight: 600;
    letter-spacing: 0.6px; line-height: 24px; color: var(--plum); margin-bottom: 22px;
  }
  .offer-list li::before {
    content: ""; position: absolute; left: 2px; top: 6px;
    border-left: 8px solid var(--offer-red); border-top: 6px solid transparent; border-bottom: 6px solid transparent;
  }
  .offer-list li.two-line { margin-bottom: 6px; }

  .about-text {
    position: absolute; left: 62px; top: 846px; width: 400px;
    font-size: 18.5px; line-height: 29px; color: var(--plum);
  }

  .call-pin { position: absolute; left: 728px; top: 746px; width: 144px; height: 176px; }
  .call-label {
    position: absolute; left: 752px; top: 782px; width: 96px; text-align: center;
    font-weight: 600; font-size: 20px; line-height: 36px; color: var(--plum);
  }

  .phone {
    position: absolute; right: 26px; top: 918px;
    font-family: "Oswald", sans-serif; font-weight: 300; font-size: 40px; letter-spacing: 2px; color: var(--plum);
  }
  .founder {
    position: absolute; right: 8px; top: 988px;
    font-family: "Cinzel", serif; font-weight: 700; font-size: 21px; letter-spacing: 0.5px; color: var(--plum);
  }
  .crew-name {
    position: absolute; right: 8px; top: 1030px;
    font-family: "Cinzel", serif; font-weight: 400; font-size: 36px; letter-spacing: 2px; color: var(--plum);
  }

  .footer { position: absolute; left: 0; top: 1105px; width: 934px; height: 95px; }
  .footer-item {
    position: absolute; display: flex; align-items: center; gap: 10px;
    font-family: "Roboto Condensed", sans-serif; font-weight: 700; font-size: 16px; color: var(--white);
  }
  .footer-item svg { flex: none; }
  .footer-web { left: 32px; top: 38px; }
  .footer-mail { left: 286px; top: 38px; }
  .footer-address { left: 530px; top: 26px; align-items: flex-start; line-height: 20px; }
  .footer-address small { font-size: 14px; display: block; }
</style>
</head>
<body>
<div class="flyer">
  <svg class="flyer-shapes" width="934" height="1200" viewBox="0 0 934 1200" aria-hidden="false">
    <defs>
      <linearGradient id="deskTone" x1="0" y1="0" x2="1" y2="1">
        <stop offset="0" stop-color="var(--photo-mid)"/>
        <stop offset="0.45" stop-color="var(--photo-light)"/>
        <stop offset="0.75" stop-color="var(--photo-mint)"/>
        <stop offset="1" stop-color="var(--photo-light)"/>
      </linearGradient>
    </defs>
    <rect width="934" height="1200" fill="var(--violet)"/>
    <polygon points="16,30 880,30 934,66 934,830 470,780 16,640" fill="url(#deskTone)" role="img" aria-label="Photo of a planner, a pen and a mug on a white desk"/>
    <polyline points="870,30 920,62 934,260" fill="none" stroke="var(--magenta-strong)" stroke-width="14"/>
    <polygon points="0,418 300,418 380,300 400,300 322,432 0,432" fill="var(--magenta-strong)"/>
    <polygon points="0,440 290,440 360,330 478,780 934,830 934,1105 0,1105" fill="var(--blush)"/>
    <polyline points="360,330 478,780 934,830" fill="none" stroke="var(--magenta-strong)" stroke-width="8"/>
    <polygon points="0,1060 60,1020 0,1020" fill="var(--magenta-strong)"/>
    <polygon points="60,1040 934,1090 934,1105 0,1105 0,1080" fill="var(--violet)"/>
    <rect x="0" y="1105" width="934" height="95" fill="var(--violet)"/>
  </svg>

  <div class="brand-box"><div class="brand-name">Ridge<br>Lass<br>Crew</div></div>

  <div class="headline-box">
    <div class="line l1">A Girls Only</div>
    <div class="line l2">After School Program</div>
    <div class="line l3">For 11-14yrs</div>
    <div class="note">as OSHC is no longer available</div>
  </div>

  <h2 class="section-title offer-title">WE OFFER</h2>
  <ul class="offer-list">
    <li>Daily meditation</li>
    <li>Healthy snacks</li>
    <li class="two-line">Organised group activity,<br>(yoga, fitness class, soccer etc.)</li>
    <li>Regular guests speakers</li>
    <li>Dedicated homework time</li>
    <li>Social media free zone</li>
  </ul>

  <h2 class="section-title about-title">ABOUT US</h2>
  <p class="about-text">The Brainchild of Rebecca Folwin, Ridge Lass Crew was created to address the growing demand for after school/school holiday super-vision for kids moving from primary into high school, when OSHC ceases to exist.</p>

  <svg class="call-pin" viewBox="0 0 144 176" aria-hidden="true">
    <path d="M72 176 L22 112 A68 68 0 1 1 122 112 Z" fill="var(--magenta-strong)"/>
    <circle cx="72" cy="70" r="50" fill="var(--white)"/>
  </svg>
  <div class="call-label">CALL<br>NOW</div>

  <div class="phone">0455817396</div>
  <div class="founder">The Brainchild of Rebecca Folwin</div>
  <div class="crew-name">Ridge Lass Crew</div>

  <footer class="footer">
    <div class="footer-item footer-web">
      <svg width="10" height="14" viewBox="0 0 10 14" aria-hidden="true"><rect x="3" y="0" width="3" height="14" fill="var(--white)"/><rect x="0" y="5" width="9" height="3" fill="var(--white)"/></svg>
      <span>http://fb.example/ridgelasscrew</span>
    </div>
    <div class="footer-item footer-mail">
      <svg width="18" height="13" viewBox="0 0 18 13" aria-hidden="true"><rect x="0.5" y="0.5" width="17" height="12" rx="1.5" fill="none" stroke="var(--white)" stroke-width="1.6"/><polyline points="1,1 9,7 17,1" fill="none" stroke="var(--white)" stroke-width="1.6"/></svg>
      <span>info@ridgelasscrew.example.au</span>
    </div>
    <div class="footer-item footer-address">
      <svg width="20" height="28" viewBox="0 0 20 28" aria-hidden="true"><path d="M10 27 C4 18 1 14 1 10 A9 9 0 0 1 19 10 C19 14 16 18 10 27 Z" fill="none" stroke="var(--white)" stroke-width="2"/><circle cx="10" cy="10" r="3.5" fill="var(--white)"/></svg>
      <span>87 Pelham Pde, Baulkham Hills<small>(across from Crestmoor Day Clinic)</small></span>
    </div>
  </footer>
</div>
</body>
</html>
```